Real Estate Company Looking for Business Card Designs for 3 Executives

Hello!
Thanks so much for considering our project! We are a real estate investment company located in Edmonton, Alberta called Bellhaven Group of Companies. We invest/develop both commercial and residential real estate and are looking to create 3 DOUBLE-SIDED business cards for 3 top executives in the company! (for some reason it won't let us select the double-sided option, but yes, the cards are double sided and would be happy to tip extra)

We have certain guidelines that we want our business cards to for sure follow - the back of the Business card has to be the Black Background Version of the Logo which has already been designed and linked as a file (first file). We want the entire back of the card to simply just be the black background logo. In terms of the front of the card, would like to see a smaller version of the white background logo (linked as the second file) in the top left hand corner - of course, feel free to get creative and we can make revisions together along the way! and Then after that, just text. We want the card to be sharp, clean, easy on the eyes and highly professional looking. We would like the card to include the Full name of the Company (Bellhaven Group of Companies), Name of the Person, Title, Phone, Email. If possible please provide the front part of the card for 3 people:

1) Bellhaven Group of Companies, Liora Quenby, Chief Financial Officer, 780-555-0142, lioraquenby@bellhavengroup.example

2) Bellhaven Group of Companies, Tobias Quenby, Chief Executive Officer, 780-555-0187, tobiasquenby@bellhavengroup.example

3) Bellhaven Group of Companies, Rui Delcourt, Chief Operations Officer, 587-555-0163, ruidelcourt@bellhavengroup.example

Thank you so much for considering our project & we look forward to seeing your designs!

```html
<!DOCTYPE html>
<html lang="en">
<head>
<meta charset="utf-8">
<title>Bellhaven Group of Companies — Business Card</title>
<link rel="stylesheet" href="https://fonts.googleapis.com/css2?family=Arimo:wght@400;700&family=Tinos:wght@400;700&display=swap">
<style>
  :root {
    --stage: #d9d9d9;
    --card-dark: #1f1f1f;
    --card-dark-mark: #2a2a2a;
    --card-light: #ffffff;
    --card-light-mark: #f1f1f1;
    --ink: #1b1b1b;
    --ink-soft: #333333;
    --paper: #ffffff;
  }
  * { box-sizing: border-box; margin: 0; padding: 0; }
  html, body { width: 1200px; height: 900px; overflow: hidden; }
  body {
    background: var(--stage);
    font-family: "Arimo", Arial, sans-serif;
    display: flex;
    flex-direction: column;
    align-items: center;
    justify-content: center;
    gap: 30px;
  }
  .card {
    position: relative;
    width: 700px;
    height: 400px;
    border-radius: 22px;
    overflow: hidden;
  }
  .card-back { background: var(--card-dark); }
  .card-front { background: var(--card-light); }

  .backdrop-word {
    position: absolute;
    font-family: "Tinos", "Times New Roman", serif;
    font-weight: 700;
    font-size: 300px;
    line-height: 1;
    letter-spacing: -6px;
    white-space: nowrap;
  }
  .card-back .backdrop-word { color: var(--card-dark-mark); right: -80px; top: 40px; }
  .card-front .backdrop-word { color: var(--card-light-mark); right: -120px; top: 60px; }

  .wordmark {
    position: absolute;
    font-family: "Tinos", "Times New Roman", serif;
    font-weight: 400;
    text-transform: uppercase;
    text-align: center;
  }
  .wordmark-name { display: block; letter-spacing: 0.32em; }
  .wordmark-tag { display: block; letter-spacing: 0.24em; }

  .card-back .wordmark {
    color: var(--paper);
    left: 50%; top: 50%;
    transform: translate(-50%, -50%);
  }
  .card-back .wordmark-name { font-size: 44px; }
  .card-back .wordmark-tag { font-size: 14px; margin-top: 10px; }

  .card-front .wordmark {
    color: var(--ink);
    left: 40px; top: 46px;
    text-align: left;
  }
  .card-front .wordmark-name { font-size: 30px; }
  .card-front .wordmark-tag { font-size: 10px; margin-top: 7px; }

  .holder { position: absolute; left: 52px; top: 182px; color: var(--ink); }
  .holder-name {
    font-family: "Tinos", "Times New Roman", serif;
    font-weight: 700;
    font-size: 30px;
    letter-spacing: 0.02em;
    text-transform: uppercase;
  }
  .holder-title { font-size: 18px; color: var(--ink-soft); margin-top: 4px; }

  .contact-list { position: absolute; left: 52px; top: 284px; list-style: none; }
  .contact-list li {
    display: flex; align-items: center; gap: 12px;
    font-size: 19px; color: var(--ink); margin-bottom: 12px;
  }
  .contact-list svg { width: 18px; height: 18px; flex: none; }

  .website {
    position: absolute; right: 40px; top: 150px;
    display: flex; align-items: center; gap: 8px;
    font-size: 16px; color: var(--ink);
  }
  .website svg { width: 14px; height: 14px; }
</style>
</head>
<body>

  <section class="card card-back" aria-label="Card back">
    <span class="backdrop-word" aria-hidden="true">BELL</span>
    <div class="wordmark">
      <span class="wordmark-name">Bellhaven</span>
      <span class="wordmark-tag">Group of Companies</span>
    </div>
  </section>

  <section class="card card-front" aria-label="Card front">
    <span class="backdrop-word" aria-hidden="true">BELL</span>
    <div class="wordmark">
      <span class="wordmark-name">Bellhaven</span>
      <span class="wordmark-tag">Group of Companies</span>
    </div>

    <div class="holder">
      <p class="holder-name">Tobias Quenby</p>
      <p class="holder-title">Chief Executive Officer</p>
    </div>

    <ul class="contact-list">
      <li>
        <svg viewBox="0 0 24 24" aria-hidden="true"><path fill="#1b1b1b" d="M6.6 10.8a15.2 15.2 0 0 0 6.6 6.6l2.2-2.2c.3-.3.7-.4 1-.2 1.1.4 2.3.6 3.6.6.6 0 1 .4 1 1V20c0 .6-.4 1-1 1A17 17 0 0 1 3 4c0-.6.4-1 1-1h3.5c.6 0 1 .4 1 1 0 1.3.2 2.5.6 3.6.1.3 0 .7-.2 1z"/></svg>
        780-555-0187
      </li>
      <li>
        <svg viewBox="0 0 24 24" aria-hidden="true"><path fill="#1b1b1b" d="M2 5h20v14H2z"/><path fill="none" stroke="#fff" stroke-width="1.6" d="M2.5 5.5 12 13l9.5-7.5M2.5 18.5l7-6.5M21.5 18.5l-7-6.5"/></svg>
        tobiasquenby@bellhavengroup.example
      </li>
    </ul>

    <div class="website">
      <svg viewBox="0 0 24 24" aria-hidden="true"><circle cx="12" cy="12" r="10" fill="#1b1b1b"/><path fill="none" stroke="#fff" stroke-width="1.4" d="M2 12h20M12 2c3 3 3 17 0 20M12 2c-3 3-3 17 0 20"/></svg>
      www.bellhavengroup.example
    </div>
  </section>

</body>
</html>
```